Home Remodeler Needs a Website!

Single page (plus contact form) website for small home remodeling company. He's got a few pictures he'd like on the site and needs some basic text. He likes clean, simple designs and is "more traditional" in his stylistic preferences. Most of his business comes from word-of-mouth advertising and so the site is just something he needs for people to feel more comfortable with his business.

Target Market(s)

People who want to remodel their homes

Coding

Coded - Design and coding required

Number of Pages Required

2 page

Requirements
Must have
• Main page to include some or all of the attached images, contact page. Neutral colors. Old domain: lindcroftmeadowbuild.com New domain: qm-ventureworks.com You can pull text from the old site or update it.
Should not have
• No loud colors/loud visual elements

```html
<!DOCTYPE html>
<html lang="en">
<head>
<meta charset="utf-8">
<title>Lindcroft Meadow Homes</title>
<link href="https://fonts.googleapis.com/css2?family=Nunito+Sans:wght@400;600;700;800&family=Varela+Round&display=swap" rel="stylesheet">
<style>
:root{
  --orange:#f7882f;
  --ink:#111111;
  --text:#3a3a3a;
  --grey-band:#efefef;
  --grey-line:#8c8c8c;
  --field:#eeeeee;
  --white:#ffffff;
  --black:#000000;
}
*{margin:0;padding:0;box-sizing:border-box}
html,body{width:1200px;height:3465px;overflow:hidden;background:var(--white)}
body{position:relative;font-family:"Nunito Sans",Arial,sans-serif;color:var(--ink)}
.abs{position:absolute}

/* header */
.site-header{position:absolute;left:0;top:0;width:1200px;height:90px;background:var(--white);z-index:5}
.brand{position:absolute;left:59px;top:31px;font-size:22px;font-weight:400;letter-spacing:.2px;color:var(--ink)}
.nav a{position:absolute;top:37px;font-size:12px;color:var(--ink);text-decoration:none;letter-spacing:.3px}
.header-phone{position:absolute;left:948px;top:30px;display:flex;align-items:center;gap:10px;font-family:"Varela Round",sans-serif;font-size:18px;letter-spacing:1px}
.icon-round{width:32px;height:32px;border-radius:50%;background:#7a7a7a;display:flex;align-items:center;justify-content:center}

/* hero */
.hero{position:absolute;left:0;top:90px;width:1200px;height:720px}
.hero-photo{position:absolute;inset:0;clip-path:polygon(0 0,100% 0,100% 599px,50% 690px,0 599px)}
.hero-photo .left{position:absolute;left:0;top:0;width:600px;height:100%;background:linear-gradient(160deg,#8fa3a8 0%,#6c7f80 45%,#5d5a50 100%)}
.hero-photo .right{position:absolute;left:600px;top:0;width:600px;height:100%;background:linear-gradient(200deg,#7c6a55 0%,#3e3126 55%,#2a231d 100%)}
.hero-photo .shade{position:absolute;inset:0;background:rgba(0,0,0,.18)}
.hero-title{position:absolute;left:0;top:197px;width:1200px;text-align:center;color:var(--white);font-size:61px;font-weight:700;line-height:66px;letter-spacing:.5px}
.hero-sub{position:absolute;left:0;top:340px;width:1200px;text-align:center;color:var(--white);font-size:28px}
.btn-orange{position:absolute;left:507px;top:385px;width:167px;height:39px;border-radius:20px;background:var(--orange);color:var(--white);font-size:12px;font-weight:800;display:flex;align-items:center;justify-content:center;letter-spacing:.4px}
.hero-arrow{position:absolute;top:258px}
.chevron{position:absolute;left:0;width:1200px}
.line-orange{fill:none;stroke:var(--orange);stroke-width:7}
.line-grey{fill:none;stroke:var(--grey-line);stroke-width:3}

/* about */
.about-photo-a{position:absolute;left:116px;top:861px;width:376px;height:366px;border-top-left-radius:110px;background:linear-gradient(180deg,#6e4f33 0%,#4a3322 45%,#141414 100%)}
.about-photo-b{position:absolute;left:293px;top:1038px;width:291px;height:256px;background:linear-gradient(180deg,#93a7a8 0%,#b9bdb4 55%,#6f6a60 100%)}
.about-text{position:absolute;left:640px;top:884px;width:475px}
.about-text h2{font-size:39px;font-weight:600;letter-spacing:-.3px}
.rule{width:42px;height:3px;background:var(--ink);margin-top:12px}
.about-text p{font-size:12.6px;line-height:25.2px;color:var(--text);margin-top:28px}
.about-text p + p{margin-top:25px}

/* services */
.services{position:absolute;left:0;top:1396px;width:1200px;height:790px;background:var(--grey-band)}
.section-title{position:absolute;left:0;width:1200px;text-align:center;font-size:37px;font-weight:600;letter-spacing:-.3px}
.section-rule{position:absolute;left:579px;width:42px;height:3px;background:var(--ink)}
.services-lead{position:absolute;left:220px;top:1540px;width:760px;text-align:center;font-size:13.6px;line-height:25px;color:var(--text)}
.svc{position:absolute;font-size:18px;font-weight:600;line-height:25px;color:var(--ink)}
.svc.left{text-align:right;right:918px}
.svc.right{left:907px}
.circle-photo{position:absolute;left:410px;top:1653px;width:380px;height:380px;border-radius:50%;background:linear-gradient(150deg,#2b4c7c 0%,#7a7c80 40%,#5a3a27 75%,#9a6a3d 100%)}

/* projects */
.project{position:absolute;top:2350px;width:343px;height:265px;display:flex;align-items:center;justify-content:center;color:var(--white);font-size:22px;font-weight:800;letter-spacing:.5px}
.project span{position:relative}
.project::before{content:"";position:absolute;inset:0;background:rgba(0,0,0,.2)}
.p-bath{left:81px;background:linear-gradient(180deg,#8c9b9c 0%,#6c6c64 100%)}
.p-kitchen{left:438px;background:linear-gradient(160deg,#2c4d7b 0%,#6e6f72 50%,#4e3324 100%)}
.p-res{left:791px;background:linear-gradient(180deg,#7a6c5a 0%,#a09a8e 55%,#574a3a 100%)}
.dot{position:absolute;width:12px;height:12px;border-radius:50%;background:#cccccc}

/* contact */
.contact{position:absolute;left:0;top:2733px;width:1200px;height:604px;background:linear-gradient(180deg,#ef8a3c 0%,#f0873a 100%)}
.contact-title{color:var(--white)}
.contact-phone{position:absolute;top:2883px;display:flex;align-items:center;gap:8px;color:var(--white);font-family:"Varela Round",sans-serif;font-size:21px;letter-spacing:.5px}
.icon-black{width:32px;height:32px;border-radius:50%;background:var(--black);display:flex;align-items:center;justify-content:center}
.field{position:absolute;background:var(--field);border:1px solid #d8d8d8;font-size:13px;color:#6a6a6a;padding:16px 22px}
.btn-send{position:absolute;left:499px;top:3213px;width:184px;height:50px;border-radius:25px;background:var(--black);color:var(--white);font-size:17px;letter-spacing:1.5px;display:flex;align-items:center;justify-content:center}

/* footer */
.site-footer{position:absolute;left:0;top:3337px;width:1200px;height:128px;background:var(--black);color:var(--white)}
.site-footer a{position:absolute;top:50px;color:var(--white);text-decoration:none;font-size:12.5px;letter-spacing:.3px}
.legal{position:absolute;left:646px;top:53px;font-size:10px}
.social{position:absolute;top:43px;width:32px;height:32px;border-radius:50%;background:var(--white)}
</style>
</head>
<body>

<header class="site-header">
  <div class="brand"><strong>LINDCROFT</strong> MEADOW HOMES</div>
  <nav class="nav">
    <a style="left:426px">HOME</a>
    <a style="left:531px">SERVICES</a>
    <a style="left:651px">ABOUT US</a>
    <a style="left:777px">CONTACT US</a>
  </nav>
  <div class="header-phone">
    <span class="icon-round"><svg width="16" height="16" viewBox="0 0 24 24"><path style="fill:#fff" d="M6.6 10.8c1.4 2.8 3.8 5.1 6.6 6.6l2.2-2.2c.3-.3.7-.4 1-.2 1.1.4 2.3.6 3.6.6.6 0 1 .4 1 1V20c0 .6-.4 1-1 1C10.6 21 3 13.4 3 4c0-.6.4-1 1-1h3.5c.6 0 1 .4 1 1 0 1.3.2 2.5.6 3.6.1.3 0 .7-.2 1z"/></svg></span>
    555-204-7180
  </div>
</header>

<section class="hero">
  <div class="hero-photo" role="img" aria-label="Photo of a remodeled bathroom with soaking tub beside an open living space with polished concrete floor">
    <div class="left"></div><div class="right"></div><div class="shade"></div>
  </div>
  <svg class="hero-arrow" style="left:18px" width="30" height="56" viewBox="0 0 30 56"><path d="M28 2 2 28l26 26" style="fill:none;stroke:#fff;stroke-width:2.5"/></svg>
  <svg class="hero-arrow" style="left:1148px" width="30" height="56" viewBox="0 0 30 56"><path d="M2 2l26 26L2 54" style="fill:none;stroke:#fff;stroke-width:2.5"/></svg>
  <h1 class="hero-title">WELCOME TO LINDCROFT<br>MEADOW HOMES</h1>
  <p class="hero-sub">Home Renovate&nbsp; Starts Here!</p>
  <div class="btn-orange">CONTACT US</div>
  <svg class="chevron" style="top:590px" width="1200" height="130" viewBox="0 0 1200 130">
    <polyline class="line-orange" points="0,9 600,100 1200,9"/>
    <polyline class="line-grey" points="255,57 600,114 945,57"/>
  </svg>
</section>

<section class="about">
  <div class="about-photo-a" role="img" aria-label="Photo of a kitchen with wooden cabinets and dark counters"></div>
  <div class="about-photo-b" role="img" aria-label="Photo of a bathroom with tiled tub surround"></div>
  <div class="about-text">
    <h2>Lindcroft Meadow Homes</h2>
    <div class="rule"></div>
    <p>When you want affordable, quality home construction services; think of us to do the job. Since 1981 Gordon Hale has built and remodeled over 400 homes and businesses. Let us be your contractor for the next project you start. When quality, value and personal attention to detail are important With over 20 years experience in residential and commercial construction, you can trust your project to Lindcroft Meadow Homes.</p>
    <p>"DON'T TINKER AROUND"<br>I have built my business with a partnership of clients, employees, subcontractors, suppliers and inspectors. Since each project is unique, this partnership brings creative ideas to your home. I have deep "hands on" history in construction from foundations to final finishing touches.</p>
  </div>
</section>

<section class="services"></section>
<h2 class="section-title" style="top:1467px">Commercial &amp; Residential Contracting</h2>
<div class="section-rule" style="top:1521px"></div>
<p class="services-lead">Providing services for roofing, window replacement, electrical, air conditioning and plumbing upgrades, painting, gutters, concrete work plumbing upgrades, painting, gutters, concrete work</p>

<svg class="abs" style="left:0;top:1620px" width="1200" height="450" viewBox="0 1620 1200 450">
  <circle cx="600" cy="1843" r="206" style="fill:none;stroke:#bdbdbd;stroke-width:3"/>
  <g style="fill:none;stroke:#777;stroke-width:1.5">
    <polyline points="322,1699 360,1699 411,1748"/>
    <polyline points="322,1840 392,1840"/>
    <polyline points="322,1984 360,1984 411,1935"/>
    <polyline points="870,1699 834,1699 784,1748"/>
    <polyline points="870,1840 808,1840"/>
    <polyline points="870,1984 834,1984 784,1935"/>
  </g>
  <g style="fill:#fff;stroke:var(--orange);stroke-width:3.5">
    <circle cx="316" cy="1699" r="6"/><circle cx="315" cy="1840" r="6"/><circle cx="314" cy="1984" r="6"/>
    <circle cx="878" cy="1699" r="6"/><circle cx="878" cy="1840" r="6"/><circle cx="880" cy="1984" r="6"/>
  </g>
</svg>
<div class="circle-photo" role="img" aria-label="Photo of a kitchen with stainless refrigerator and dark wood cabinets"></div>
<div class="svc left" style="top:1679px">Pre Construction<br>Consultation</div>
<div class="svc left" style="top:1828px">New Construction</div>
<div class="svc left" style="top:1960px">Remodeling<br>Kitchen &amp; Baths</div>
<div class="svc right" style="top:1687px">Additions</div>
<div class="svc right" style="top:1828px">Porches and Decks</div>
<div class="svc right" style="top:1953px">Specializing in historic<br>renovations</div>

<svg class="chevron" style="top:2040px" width="1200" height="150" viewBox="0 0 1200 150">
  <polygon points="0,18 600,119 1200,18 1200,150 0,150" style="fill:var(--white)"/>
  <polyline class="line-orange" points="0,18 600,119 1200,18"/>
  <polyline class="line-grey" points="255,74 600,128 945,74"/>
</svg>

<h2 class="section-title" style="top:2248px">Recent Projects</h2>
<div class="section-rule" style="top:2301px"></div>
<div class="project p-bath" role="img" aria-label="Photo of a remodeled bathroom"><span>BATHROOM</span></div>
<div class="project p-kitchen" role="img" aria-label="Photo of a remodeled kitchen"><span>KITCHEN</span></div>
<div class="project p-res" role="img" aria-label="Photo of a residential open living area"><span>RESIDENTIAL</span></div>
<div class="dot" style="left:580px;top:2642px;background:var(--black)"></div>
<div class="dot" style="left:601px;top:2662px"></div>
<div class="dot" style="left:621px;top:2662px"></div>

<section class="contact" role="img" aria-label="Faint photo of kitchen cabinetry under an orange tint"></section>
<h2 class="section-title contact-title" style="top:2797px;font-size:38px">Contact Us</h2>
<div class="section-rule" style="top:2851px;background:var(--white)"></div>
<div class="contact-phone" style="left:401px"><span class="icon-black"><svg width="16" height="16" viewBox="0 0 24 24"><path style="fill:#fff" d="M6.6 10.8c1.4 2.8 3.8 5.1 6.6 6.6l2.2-2.2c.3-.3.7-.4 1-.2 1.1.4 2.3.6 3.6.6.6 0 1 .4 1 1V20c0 .6-.4 1-1 1C10.6 21 3 13.4 3 4c0-.6.4-1 1-1h3.5c.6 0 1 .4 1 1 0 1.3.2 2.5.6 3.6.1.3 0 .7-.2 1z"/></svg></span>555-204-7180</div>
<div class="contact-phone" style="left:621px"><span class="icon-black"><svg width="16" height="16" viewBox="0 0 24 24"><path style="fill:#fff" d="M6.6 10.8c1.4 2.8 3.8 5.1 6.6 6.6l2.2-2.2c.3-.3.7-.4 1-.2 1.1.4 2.3.6 3.6.6.6 0 1 .4 1 1V20c0 .6-.4 1-1 1C10.6 21 3 13.4 3 4c0-.6.4-1 1-1h3.5c.6 0 1 .4 1 1 0 1.3.2 2.5.6 3.6.1.3 0 .7-.2 1z"/></svg></span>555-204-7391</div>

<form class="contact-form">
  <div class="field" style="left:198px;top:2964px;width:400px;height:48px">First Name*</div>
  <div class="field" style="left:609px;top:2964px;width:401px;height:48px">Last Name*</div>
  <div class="field" style="left:198px;top:3022px;width:400px;height:48px">Email address*</div>
  <div class="field" style="left:609px;top:3022px;width:401px;height:48px">Phone*</div>
  <div class="field" style="left:198px;top:3083px;width:817px;height:107px">Message</div>
  <div class="btn-send">SEND</div>
</form>

<footer class="site-footer">
  <a style="left:134px">HOME</a>
  <a style="left:243px">SERVICES</a>
  <a style="left:373px">ABOUT US</a>
  <a style="left:507px">CONTACT</a>
  <div class="legal">© 2021 Lindcroft Meadow Homes &nbsp;|&nbsp; Legal &nbsp;|&nbsp; Term of Use</div>
  <div class="social" style="left:977px"></div>
  <div class="social" style="left:1019px"></div>
  <div class="social" style="left:1061px"></div>
</footer>

</body>
</html>
```